Hardcore nerd needs to stand out in a sea of dull Defence business cards

Wombarra Devices is a new Australian consulting engineering company that turns research and theory into practical systems. No evangelistic fluff, just mathematics and physics into electronic and optical circuits for consumer products, scientific research or Defence applications.

We already have a recognised logo (provided) which is often dark blue/black on a light background but we're open to other combinations. (Us engineers tend to have limited aesthetic imagination :)

Some of our recent products have included:
* Instrumentation for electrical testing,
* Radar jammers,
* GPS antenna design,
* Satellite tracking systems,
* High power lasers

We're open to both single and double-sided designs - happy to be convinced either way.

P.S. Another group is working on the web page, so - alas - our web site is currently of no use for images/ideas...

Target Market(s)

Engineering managers,
Scientists

Contact Information for Business Card

Dr Colin Harte
R&D Engineer

colin@wombarradevices.com.au
0427 563 710

PO Box XXX (to be confirmed)
Kelsby ACT 2917
Australia

Font styles to use
Serif
Sans Serif

Colors

Designer to choose colors to be used in the design.

Requirements
Must have
• My contact details!
• I've had many (great) "bold and plain" designs submitted already, so feel free to be artistically creative :)
• Happy to take advice re fonts/colours/printability etc.
Nice to have
• I'm not sure if "lists" are more at home on a CV than a business card, but representative services include:
• Applied electromagnetics
• RF and high speed electronics
• Signal and image processing
• Electro-optical and laser systems
• Concept-to-prototype design services
• If you're considering double sided cards, then often measuring/alignment grids/rulers feature on the back of similar cards.
• e.g. https://www.veltranoptics.example/newgrouppage9.cfm?objectgroup_id=4183
• https://www.veltranoptics.example/newgrouppage9.cfm?objectgroup_ID=4185
• ..or even a "Smith chart" (google will return lots)
• Generic images to represent a capability might work - googling images associated with keyword for each of these areas might help:
• - "passive radar", "phased array", "fdtd", "vircator"
• RF and high speed electronic design
• - "smith chart", "microstrip circuits", "dimensioned drawing", "electronic schematic"
• - "dft", "iir filter"
• - "optical cavity". "laser energy level diagram"
• Background/watermarked images outlines/wireframes/schematics would probably look OK.
Should not have
• If a list of projects/services is provided, it is important not to make the client feel that this is "all" the company can do. Engineering design is a creative discipline (like graphics :)
• Please, no stock "military" snaps like planes, missiles, etc!

```html
<!DOCTYPE html>
<html lang="en">
<head>
<meta charset="utf-8">
<title>Wombarra Devices – Business Card</title>
<link href="https://fonts.googleapis.com/css2?family=Lato:wght@400;700;900&display=swap" rel="stylesheet">
<style>
  :root {
    --navy: #0b1f63;
    --navy-deep: #081751;
    --navy-soft: #243a86;
    --paper: #fbf7f6;
    --ink: #1c1c24;
    --white: #ffffff;
    --stage: #dcdde0;
  }
  * { box-sizing: border-box; margin: 0; padding: 0; }
  html, body {
    width: 1200px;
    height: 782px;
    overflow: hidden;
    background: var(--stage);
    font-family: "Lato", Arial, sans-serif;
  }
  .canvas {
    width: 1200px;
    height: 782px;
    display: flex;
    align-items: center;
    justify-content: center;
    gap: 40px;
  }
  .card {
    width: 540px;
    height: 309px;
    position: relative;
    overflow: hidden;
    box-shadow: 0 6px 18px rgba(0,0,0,0.25);
  }

  /* Front */
  .card-front { background: var(--paper); color: var(--ink); }
  .brand {
    position: absolute;
    left: 30px;
    top: 30px;
    display: flex;
    align-items: flex-end;
    gap: 14px;
  }
  .brand-dot {
    width: 96px;
    height: 96px;
    border-radius: 50%;
    background: var(--navy);
    flex: none;
  }
  .brand-name {
    font-weight: 900;
    color: var(--navy);
    text-transform: uppercase;
    line-height: 1;
    padding-bottom: 2px;
  }
  .brand-name .line-1 { display: block; font-size: 36px; letter-spacing: 0.5px; }
  .brand-name .line-2 { display: block; font-size: 17px; letter-spacing: 8.2px; margin-top: 3px; }

  .contact {
    position: absolute;
    left: 144px;
    top: 150px;
  }
  .person-name {
    font-weight: 900;
    font-size: 18px;
    color: var(--navy);
    text-transform: uppercase;
    line-height: 1.1;
  }
  .person-role {
    font-size: 13px;
    color: var(--ink);
    margin-bottom: 6px;
  }
  .contact-list { list-style: none; }
  .contact-list li {
    display: flex;
    align-items: center;
    gap: 7px;
    font-size: 15px;
    line-height: 1.55;
    color: var(--ink);
  }
  .contact-list li.address { margin-left: -14px; }
  .contact-list svg {
    width: 12px;
    height: 12px;
    fill: var(--navy);
    flex: none;
  }

  /* Back */
  .card-back { background: var(--navy); }
  .back-texture {
    position: absolute;
    inset: 0;
    background:
      radial-gradient(circle at 72% 62%, rgba(60,88,170,0.45) 0%, rgba(60,88,170,0) 45%),
      radial-gradient(circle at 15% 20%, rgba(46,70,150,0.35) 0%, rgba(46,70,150,0) 50%),
      linear-gradient(160deg, var(--navy-soft) 0%, var(--navy) 50%, var(--navy-deep) 100%);
  }
  .back-mark {
    position: absolute;
    left: 320px;
    top: 168px;
    display: flex;
    align-items: center;
    gap: 10px;
  }
  .back-dot {
    width: 40px;
    height: 40px;
    border-radius: 50%;
    background: var(--white);
    flex: none;
  }
  .back-name {
    font-weight: 900;
    font-size: 15px;
    letter-spacing: 0.5px;
    color: var(--white);
    text-transform: uppercase;
  }
</style>
</head>
<body>
<main class="canvas">

  <section class="card card-front">
    <div class="brand">
      <span class="brand-dot"></span>
      <span class="brand-name"><span class="line-1">Wombarra</span><span class="line-2">Devices</span></span>
    </div>

    <div class="contact">
      <p class="person-name">Dr Colin Harte</p>
      <p class="person-role">R&amp;D Engineer</p>
      <ul class="contact-list">
        <li>
          <svg viewBox="0 0 24 24" aria-hidden="true"><path d="M6.6 10.8a15.1 15.1 0 0 0 6.6 6.6l2.2-2.2a1 1 0 0 1 1-.25 11.4 11.4 0 0 0 3.6.57 1 1 0 0 1 1 1V20a1 1 0 0 1-1 1A17 17 0 0 1 3 4a1 1 0 0 1 1-1h3.5a1 1 0 0 1 1 1c0 1.25.2 2.45.57 3.6a1 1 0 0 1-.25 1z"/></svg>
          0427 563 710
        </li>
        <li>
          <svg viewBox="0 0 24 24" aria-hidden="true"><path d="M2 5h20v14H2z M2 5l10 8 10-8" stroke="#fbf7f6" stroke-width="1.5"/></svg>
          colin@wombarradevices.com.au
        </li>
        <li class="address">
          <svg viewBox="0 0 24 24" aria-hidden="true"><path d="M12 2a7 7 0 0 0-7 7c0 5.2 7 13 7 13s7-7.8 7-13a7 7 0 0 0-7-7zm0 9.5A2.5 2.5 0 1 1 12 6.5a2.5 2.5 0 0 1 0 5z"/></svg>
          PO Box XXX&nbsp; Kelsby ACT 2917, Australia
        </li>
      </ul>
    </div>
  </section>

  <section class="card card-back">
    <div class="back-texture" role="img" aria-label="Faint repeating brand pattern in navy tones covering the card back"></div>
    <div class="back-mark">
      <span class="back-dot"></span>
      <span class="back-name">Wombarra Devices</span>
    </div>
  </section>

</main>
</body>
</html>
```